Business card design for Qorvane Engineering Tandem

We need a new business card design along with all the necessary to place an order. The company is Qorvane Engineering Tandem and we recently updated our logo.

```html
<!DOCTYPE html>
<html lang="en">
<head>
<meta charset="utf-8">
<title>Qorvane Engineering Tandem – Business Card</title>
<link rel="stylesheet" href="https://fonts.googleapis.com/css2?family=Poppins:wght@400;600;700&display=swap">
<style>
  :root {
    --page: #ffffff;
    --card: #ffffff;
    --steel: #949494;
    --steel-dark: #8f8f8f;
    --white: #ffffff;
    --divider: rgba(255,255,255,0.7);
    --shadow: rgba(0,0,0,0.35);
  }
  * { margin: 0; padding: 0; box-sizing: border-box; }
  html, body {
    width: 979px; height: 1200px; overflow: hidden;
    background: var(--page);
    font-family: "Poppins", sans-serif;
  }
  .canvas { position: relative; width: 979px; height: 1200px; }
  .card {
    position: absolute; left: 117px; width: 735px; height: 420px;
    background: var(--card); overflow: hidden;
    box-shadow: 8px 8px 10px var(--shadow);
  }
  .card-front { top: 138px; }
  .card-back { top: 638px; }

  .wordmark { position: absolute; color: var(--steel); font-weight: 700; line-height: 1; display: flex; align-items: center; gap: 16px; white-space: nowrap; }
  .wordmark .mark { background: var(--steel); flex: none; }
  .wordmark .name { display: flex; flex-direction: column; }
  .wordmark .name-main { letter-spacing: 0.05em; }
  .wordmark .name-sub { letter-spacing: 0.01em; }

  .card-front .wordmark { left: 50%; top: 50%; transform: translate(-50%, -50%); }
  .card-front .mark { width: 52px; height: 52px; }
  .card-front .name-main { font-size: 66px; }
  .card-front .name-sub { font-size: 24px; margin-top: 2px; }

  .card-back .wordmark { left: 64px; top: 62px; gap: 12px; }
  .card-back .mark { width: 34px; height: 34px; }
  .card-back .name-main { font-size: 44px; }
  .card-back .name-sub { font-size: 16px; margin-top: 1px; }

  .info-band {
    position: absolute; left: 0; bottom: 0; width: 100%; height: 233px;
    background: var(--steel-dark); color: var(--white);
  }
  .holder { position: absolute; right: 393px; top: 80px; text-align: right; }
  .holder-name { font-size: 24px; font-weight: 700; line-height: 1.1; }
  .holder-role { font-size: 16px; font-weight: 400; }
  .divider { position: absolute; left: 366px; top: 40px; width: 1.5px; height: 142px; background: var(--divider); }
  .contacts { position: absolute; left: 385px; top: 72px; list-style: none; font-size: 17.5px; }
  .contacts li { display: flex; align-items: center; gap: 16px; height: 26.5px; }
  .contacts svg { width: 17px; height: 17px; fill: var(--white); flex: none; }
  .address { position: absolute; left: 0; width: 100%; bottom: 10px; text-align: center; font-size: 17px; }
</style>
</head>
<body>
<div class="canvas">
  <section class="card card-front">
    <div class="wordmark">
      <span class="mark"></span>
      <span class="name">
        <span class="name-main">QORVANE</span>
        <span class="name-sub">ENGINEERING TANDEM</span>
      </span>
    </div>
  </section>

  <section class="card card-back">
    <div class="wordmark">
      <span class="mark"></span>
      <span class="name">
        <span class="name-main">QORVANE</span>
        <span class="name-sub">ENGINEERING TANDEM</span>
      </span>
    </div>

    <div class="info-band">
      <div class="holder">
        <p class="holder-name">Name Name</p>
        <p class="holder-role">CEO</p>
      </div>
      <div class="divider"></div>
      <ul class="contacts">
        <li>
          <svg viewBox="0 0 24 24" aria-hidden="true"><path d="M6.6 10.8a15.1 15.1 0 0 0 6.6 6.6l2.2-2.2a1 1 0 0 1 1-.25 11.4 11.4 0 0 0 3.6.57 1 1 0 0 1 1 1V20a1 1 0 0 1-1 1A17 17 0 0 1 3 4a1 1 0 0 1 1-1h3.5a1 1 0 0 1 1 1c0 1.25.2 2.45.57 3.57a1 1 0 0 1-.25 1z"/></svg>
          <span>000-000-0000</span>
        </li>
        <li>
          <svg viewBox="0 0 24 24" aria-hidden="true"><path d="M2 5h20v2.2l-10 6-10-6z"/><path d="M2 9.5l10 6 10-6V19H2z"/></svg>
          <span>info@qorvane.com</span>
        </li>
        <li>
          <svg viewBox="0 0 24 24" aria-hidden="true"><path d="M12 2a10 10 0 1 0 0 20 10 10 0 0 0 0-20zm6.9 6h-2.9a15.7 15.7 0 0 0-1.4-3.6A8 8 0 0 1 18.9 8zM12 4a14 14 0 0 1 1.9 4h-3.8A14 14 0 0 1 12 4zM4.3 14a8.2 8.2 0 0 1 0-4h3.4a16.5 16.5 0 0 0 0 4zm.8 2h2.9a15.7 15.7 0 0 0 1.4 3.6A8 8 0 0 1 5.1 16zM8 8H5.1a8 8 0 0 1 4.3-3.6A15.7 15.7 0 0 0 8 8zm4 12a14 14 0 0 1-1.9-4h3.8A14 14 0 0 1 12 20zm2.3-6H9.7a14.7 14.7 0 0 1 0-4h4.6a14.7 14.7 0 0 1 0 4zm.3 5.6a15.7 15.7 0 0 0 1.4-3.6h2.9a8 8 0 0 1-4.3 3.6zM16.3 14a16.5 16.5 0 0 0 0-4h3.4a8.2 8.2 0 0 1 0 4z"/></svg>
          <span>qorvane.com</span>
        </li>
      </ul>
      <p class="address">3361 Address Street, City, Country Zip code</p>
    </div>
  </section>
</div>
</body>
</html>
```